Tree Pruning Website

We need a website for a tree Arborist, pruning company called Maple Crest Canopy Works. We look after all types of trees, knock down trees and prune trees. Our target market is from domestic clients to government clients and everything in between.

We would like to see the use of our main colours which are orange and green

We are not looking forward in seeing a template that we have seen before but a unique template. We have designed 5 templates ourselves and we wish for the design community to take our designs to the next level.

We have also designed a template for things that **we are not** looking for (Version 4)

To make it fair for everyone, we are also not giving out any participation payments as we have had. One winner will take all of the payment!!!

I Have attached a image of the designs and a image of a tree.

We are just looking at the PSD file been developed. We have our own team who can slice the image up into a HTML format.

Target Market(s)

Everyone who needs to cut down a tree

Industry/Entity Type

Government

Requirements
Must have
• Logo on front page
A List of our services
jQuery slider on page
Phone Number on every page

```html
<!DOCTYPE html>
<html lang="en">
<head>
<meta charset="utf-8">
<title>Maple Crest Canopy Works</title>
<link href="https://fonts.googleapis.com/css2?family=Gelasio:ital,wght@0,400;0,700;1,400&display=swap" rel="stylesheet">
<style>
:root{
  --green:#4f8a22;
  --green-dark:#3a6d14;
  --green-text:#4c8a1f;
  --orange-top:#ffcf1a;
  --orange-bot:#f8a10a;
  --yellow-box:#f8bd0c;
  --grey-tab:#e8e8e8;
  --grey-text:#666;
  --body-text:#555;
  --white:#fff;
  --blue-top:#7fb6ee;
  --blue-bot:#2c6fc4;
  --phone:#f3b21a;
}
*{margin:0;padding:0;box-sizing:border-box}
html,body{width:1200px;height:1125px;overflow:hidden}
body{position:relative;background:#f4f4f4;font-family:'Gelasio',Georgia,serif;color:var(--body-text)}
.abs{position:absolute}

/* header */
.site-header{left:0;top:0;width:1200px;height:115px;background:var(--white)}
.brand{left:150px;top:28px;display:flex;align-items:center;gap:12px}
.brand-mark{width:58px;height:58px;border-radius:50%;background:var(--green)}
.brand-name{font-weight:700;font-size:21px;line-height:20px;color:var(--green-text);text-transform:uppercase}
.phone{right:150px;top:9px;display:flex;align-items:center;gap:10px;color:var(--phone);font-size:24px}
.main-nav{left:488px;top:47px;display:flex;gap:2px;align-items:flex-start}
.main-nav a{display:block;width:92px;height:56px;margin-top:10px;background:var(--grey-tab);color:var(--grey-text);font-size:13px;text-align:center;padding-top:11px;text-decoration:none}
.main-nav a.active{height:68px;margin-top:0;background:var(--green);color:var(--white);padding-top:22px}

/* hero */
.hero{left:0;top:115px;width:1200px;height:541px;background:var(--green);border-top:7px solid var(--green-dark)}
.slider{left:150px;top:150px;width:900px;height:375px;background:var(--white)}
.slide-copy{left:169px;top:190px;width:300px}
.slide-copy h2{font-weight:400;font-size:30px;color:var(--green-text);margin-bottom:8px}
.slide-copy p{font-size:12.2px;line-height:18.75px;color:#444}
.btn{display:flex;align-items:center;justify-content:center;gap:12px;background:linear-gradient(var(--orange-top),var(--orange-bot));color:var(--white);font-size:19px;text-decoration:none}
.slide-btn{left:169px;top:412px;width:159px;height:38px}
.dots{left:169px;top:498px;display:flex;gap:5px}
.dots span{width:7px;height:7px;background:#a6d47e}
.dots span:first-child{background:var(--green-dark)}
.slide-photo{left:487px;top:155px;width:558px;height:365px;background:linear-gradient(160deg,#8a9a88,#4f6b3a 45%,#c9cfc0 75%,#55703a)}
.slide-caption{left:487px;top:375px;width:558px;height:113px;background:rgba(40,40,30,.45);color:var(--white);font-style:italic;font-size:33px;line-height:34px;text-align:right;padding:22px 22px 0 0;text-shadow:0 1px 3px rgba(0,0,0,.6)}
.tagline{left:150px;top:547px;width:900px;text-align:center;color:var(--white);font-style:italic;font-size:23.5px;line-height:28px}

/* columns */
.col-title{font-weight:400;font-size:23px;color:var(--green-text)}
.about-photo{left:150px;top:722px;width:281px;height:131px;border:1px solid var(--green);background:linear-gradient(#9ec4e8,#c3dbef 55%,#3f6a2c 70%,#2d4c22)}
.about-text{left:150px;top:867px;width:281px;font-size:12px;line-height:18.75px;color:#666}
.about-btn{left:150px;top:1022px;width:159px;height:37px}
.services{left:459px;top:722px;width:281px;height:337px;background:var(--yellow-box);border:1px solid #e8a400;list-style:none;padding:0 9px}
.services li{height:42px;display:flex;align-items:center;gap:10px;padding-left:10px;color:var(--white);font-size:17px;border-bottom:1px solid #e3a90a}
.services li:last-child{border-bottom:none}
.thumb{width:136px;height:89px;border:1px solid var(--green)}
.view-btn{left:769px;top:919px;width:281px;height:37px}
.quote-pill{left:769px;top:984px;width:281px;height:75px;border-radius:38px;background:linear-gradient(var(--blue-top),var(--blue-bot));box-shadow:0 3px 5px rgba(0,0,0,.3);color:var(--white)}
.quote-pill .icon{left:18px;top:18px;width:38px;height:38px;border-radius:50%;background:var(--white)}
.quote-pill strong{left:67px;top:10px;font-weight:400;font-size:29px}
.quote-pill small{left:67px;top:50px;font-size:12px;color:#dbe9fa}

/* footer */
.site-footer{left:0;top:1087px;width:1200px;height:38px;background:var(--green-dark);color:var(--white);font-size:12px}
.copyright{left:150px;top:11px}
.follow{right:150px;top:9px;display:flex;align-items:center;gap:10px}
.follow span.sq{width:19px;height:19px;border-radius:3px;background:#6f9fd8}
.follow span.sq.rss{background:#f08a24}
</style>
</head>
<body>

<header class="site-header abs">
  <div class="brand abs">
    <span class="brand-mark"></span>
    <span class="brand-name">Maple Crest<br>Canopy Works</span>
  </div>
  <div class="phone abs">
    <svg width="34" height="24" viewBox="0 0 34 24"><path d="M3 8c0-5 28-5 28 0v3h-7V8H10v3H3z" fill="#ddd"/><rect x="8" y="11" width="18" height="12" rx="2" fill="#ddd"/><circle cx="17" cy="17" r="3.5" fill="#fff"/></svg>
    <span>1800 555 0142</span>
  </div>
  <nav class="main-nav abs">
    <a class="active" href="#">Home</a><a href="#">About</a><a href="#">Services</a><a href="#">Works</a><a href="#">Get a Quote</a><a href="#">Contact</a>
  </nav>
</header>

<section class="hero abs"></section>
<div class="slider abs"></div>
<div class="slide-copy abs">
  <h2>Tree Purning</h2>
  <p>Lorem ipsum dolor sit amet, consectetur adipisicing elit, sed do eiusmod tempor incididunt ut labore et dolore magna aliqua. Ut enim ad minim veniam, quis nostrud exercitation ullamco laboris nisi ut aliquip ex ea commodo consequat. Duis aute irure dolor in repre­henderit in voluptate velit esse cillum dolore eu fugiat nulla pariatur. Excepteur sint occaecat cupidatat non proident, sunt in culpa qui officia deserunt mollit anim id est laborum.</p>
</div>
<a class="btn slide-btn abs" href="#">Learn more <svg width="12" height="16"><path d="M2 2l7 6-7 6" stroke="#fff" stroke-width="3" fill="none"/></svg></a>
<div class="dots abs"><span></span><span></span><span></span><span></span></div>
<div class="slide-photo abs" role="img" aria-label="Looking up into tall pale-barked eucalyptus trees"></div>
<div class="slide-caption abs">We clean the barks of the tree<br>and make them look nice</div>
<p class="tagline abs">Maple Crest Canopy Works, consectetur adipisicing elit, sed do eiusmod tempor incididunt ut labore et dolore magna aliqua. Ut enim ad minim veniam, quis nostrud exercitation ullamco laboris nisi ut aliquip ex ea commodo consequat quis nostrud exercitation.</p>

<h3 class="col-title abs" style="left:150px;top:678px">About us</h3>
<div class="about-photo abs" role="img" aria-label="Pruned tree against a blue sky in a park"></div>
<p class="about-text abs">Lorem ipsum dolor sit amet, consectetur adipisicing elit, sed do eiusmod tempor incididunt ut labore et dolore magna aliqua. Ut enim ad minim veniam, quis nostrud exercitation ullamco laboris nisi ut aliquip ex ea commodo consequat. Duis aute irure dolor in reprehenderit in voluptate velit esse cillum dolore eu fugiat nulla pariatur.</p>
<a class="btn about-btn abs" href="#">Learn more <svg width="12" height="16"><path d="M2 2l7 6-7 6" stroke="#fff" stroke-width="3" fill="none"/></svg></a>

<h3 class="col-title abs" style="left:459px;top:678px">Our Services</h3>
<ul class="services abs">
  <li><svg width="16" height="10"><circle cx="3" cy="5" r="2" fill="#fff"/><path d="M6 5h7M10 1l4 4-4 4" stroke="#fff" stroke-width="2" fill="none"/></svg>Diagnosis</li>
  <li><svg width="16" height="10"><circle cx="3" cy="5" r="2" fill="#fff"/><path d="M6 5h7M10 1l4 4-4 4" stroke="#fff" stroke-width="2" fill="none"/></svg>Treatment</li>
  <li><svg width="16" height="10"><circle cx="3" cy="5" r="2" fill="#fff"/><path d="M6 5h7M10 1l4 4-4 4" stroke="#fff" stroke-width="2" fill="none"/></svg>Tree Purning</li>
  <li><svg width="16" height="10"><circle cx="3" cy="5" r="2" fill="#fff"/><path d="M6 5h7M10 1l4 4-4 4" stroke="#fff" stroke-width="2" fill="none"/></svg>Tree Removal</li>
  <li><svg width="16" height="10"><circle cx="3" cy="5" r="2" fill="#fff"/><path d="M6 5h7M10 1l4 4-4 4" stroke="#fff" stroke-width="2" fill="none"/></svg>Stump Removal</li>
  <li><svg width="16" height="10"><circle cx="3" cy="5" r="2" fill="#fff"/><path d="M6 5h7M10 1l4 4-4 4" stroke="#fff" stroke-width="2" fill="none"/></svg>Cabling &amp; Bracing</li>
  <li><svg width="16" height="10"><circle cx="3" cy="5" r="2" fill="#fff"/><path d="M6 5h7M10 1l4 4-4 4" stroke="#fff" stroke-width="2" fill="none"/></svg>Arborist Consults</li>
  <li><svg width="16" height="10"><circle cx="3" cy="5" r="2" fill="#fff"/><path d="M6 5h7M10 1l4 4-4 4" stroke="#fff" stroke-width="2" fill="none"/></svg>Tree Protection</li>
</ul>

<h3 class="col-title abs" style="left:768px;top:678px">Our Latest Works</h3>
<div class="thumb abs" style="left:769px;top:722px;background:linear-gradient(#9fbf7a,#6a8a46)" role="img" aria-label="Uprooted fallen tree on a lawn"></div>
<div class="thumb abs" style="left:914px;top:722px;background:linear-gradient(135deg,#4a7fb8,#4f7a2e)" role="img" aria-label="Tall tree trunk seen from below"></div>
<div class="thumb abs" style="left:769px;top:820px;background:linear-gradient(#dfe9f2,#3f7a28 40%,#2d5a1c)" role="img" aria-label="Topiary hedge shaped into a figure"></div>
<div class="thumb abs" style="left:914px;top:820px;background:linear-gradient(#5a8cc8,#b08a5c 60%,#6d4a2e)" role="img" aria-label="Arborist cutting a large log section"></div>
<a class="btn view-btn abs" href="#">View more works <svg width="12" height="16"><path d="M2 2l7 6-7 6" stroke="#fff" stroke-width="3" fill="none"/></svg></a>
<a class="quote-pill abs" href="#">
  <span class="icon abs"><svg width="38" height="38"><path d="M15 11l8 8-8 8" stroke="#1f4f8a" stroke-width="4" fill="none"/></svg></span>
  <strong class="abs">Get a Quote</strong>
  <small class="abs">Contact us about your tree needs</small>
</a>

<footer class="site-footer abs">
  <p class="copyright abs">Copyright © 2013 Maple Crest Canopy Works. All Rights Reserved.</p>
  <div class="follow abs">Follow us on <span class="sq"></span><span class="sq"></span><span class="sq rss"></span></div>
</footer>

</body>
</html>
```